Hvac and insulation company needs good looking business card design

We are hvac and insulation company and looking for a new business cards that look to today standards designs

Target Market(s)

homeowners

Industry/Entity Type

Hvac

Contact Information for Business Card

Name: Walter Brinoku
Home comfort consultant
address: 4827 Dunmore St #215 Oakland, CA 94619
office: 888-316-2790
cell: 510-742-3185
Lic.# 584261
Email: walter@corvane-hvac.com
Web: corvane-hvac.com

Requirements
Must have
• clean and sleek look
Nice to have
• simple with a clean look
Should not have
• to busy business card

```html
<!DOCTYPE html>
<html lang="en">
<head>
<meta charset="utf-8">
<title>Corvane Home Solutions – Business Card</title>
<link rel="stylesheet" href="https://fonts.googleapis.com/css2?family=Arimo:wght@400;700&display=swap">
<style>
  :root {
    --stage: #3b3b3b;
    --card-light: #ececec;
    --brand-orange: #f4831f;
    --ink: #1f1f1f;
    --muted: #8a8a8a;
    --rule: #9a9a9a;
    --white: #ffffff;
  }
  * { box-sizing: border-box; margin: 0; padding: 0; }
  html, body {
    width: 1200px; height: 900px; overflow: hidden;
    background: var(--stage);
    font-family: "Arimo", Arial, sans-serif;
  }
  .card {
    position: absolute; top: 170px;
    width: 347px; height: 561px;
    overflow: hidden;
  }
  .card--front { left: 259px; background: var(--card-light); }
  .card--back { left: 631px; background: var(--brand-orange); }

  .wordmark {
    position: absolute; left: 0; right: 0; top: 118px;
    display: flex; align-items: center; justify-content: center; gap: 12px;
  }
  .wordmark__dot {
    width: 40px; height: 40px; border-radius: 50%;
    background: var(--brand-orange);
  }
  .wordmark__name {
    font-size: 44px; font-weight: 700; color: var(--brand-orange);
    letter-spacing: -0.5px; line-height: 1;
  }
  .tagline {
    position: absolute; top: 168px; left: 122px;
    font-size: 14px; letter-spacing: 2px; color: var(--muted);
  }

  .person { position: absolute; top: 273px; left: 0; right: 0; text-align: center; }
  .person__name {
    font-size: 20px; font-weight: 700; color: var(--brand-orange); letter-spacing: 0.3px;
  }
  .person__role { margin-top: 5px; font-size: 16px; color: var(--ink); }

  .icon-row {
    position: absolute; top: 331px; left: 72px; right: 72px;
    display: flex; align-items: center; gap: 4px;
  }
  .icon-row::before, .icon-row::after {
    content: ""; flex: 1; height: 1px; background: var(--ink); opacity: .6;
  }
  .icon-row::before { margin-right: 4px; }
  .icon-row::after { margin-left: 4px; }
  .icon-row svg { width: 21px; height: 21px; display: block; }

  .contact {
    position: absolute; top: 357px; left: 0; right: 0;
    text-align: center; font-size: 15.5px; line-height: 20.5px; color: var(--ink);
  }
  .divider {
    position: absolute; top: 447px; left: 72px; right: 72px;
    height: 1px; background: var(--rule);
  }
  .address {
    position: absolute; top: 459px; left: 0; right: 0;
    text-align: center; font-size: 15.5px; line-height: 20.5px; color: var(--ink);
  }
  .license-band {
    position: absolute; left: 0; right: 0; bottom: 0; height: 50px;
    background: var(--brand-orange); color: var(--white);
    display: flex; align-items: center; justify-content: center;
    font-size: 15.5px;
  }

  .back-wordmark {
    position: absolute; left: 54px; bottom: 44px; color: var(--white);
  }
  .back-wordmark__name { font-size: 54px; font-weight: 700; line-height: 1; letter-spacing: -0.5px; }
  .back-wordmark__tagline { margin-top: 4px; font-size: 16px; letter-spacing: 2.4px; }
</style>
</head>
<body>
  <section class="card card--front">
    <div class="wordmark">
      <span class="wordmark__dot"></span>
      <span class="wordmark__name">corvane</span>
    </div>
    <div class="tagline">home solutions</div>

    <div class="person">
      <div class="person__name">WALTER BRINOKU</div>
      <div class="person__role">Home Comfort Consultant</div>
    </div>

    <div class="icon-row" aria-hidden="true">
      <svg viewBox="0 0 22 22"><circle cx="11" cy="11" r="11" fill="#f4831f"/><path d="M6 8.5h10v1.5H6zM7.5 10h7l1 4.5h-9z" fill="#fff"/><circle cx="11" cy="12.3" r="1.3" fill="#f4831f"/></svg>
      <svg viewBox="0 0 22 22"><circle cx="11" cy="11" r="11" fill="#f4831f"/><rect x="7.7" y="5" width="6.6" height="12" rx="1" fill="none" stroke="#fff" stroke-width="1.3"/><circle cx="11" cy="15" r=".7" fill="#fff"/></svg>
      <svg viewBox="0 0 22 22"><circle cx="11" cy="11" r="11" fill="#f4831f"/><rect x="5.5" y="7.5" width="11" height="7.5" fill="#fff"/><path d="M5.5 7.5l5.5 4 5.5-4" fill="none" stroke="#f4831f" stroke-width="1"/></svg>
      <svg viewBox="0 0 22 22"><circle cx="11" cy="11" r="11" fill="#f4831f"/><circle cx="11" cy="11" r="5.5" fill="#fff"/><path d="M8.5 8.5c1.5 0 2 1.5 1 2.5s.5 2 1.5 2.5M13 7c-.5 1 .5 2 1.5 2" fill="none" stroke="#f4831f" stroke-width="1.1"/></svg>
    </div>

    <div class="contact">
      <div>888-316-2790</div>
      <div>510-742-3185</div>
      <div>walter@corvane-hvac.com</div>
      <div>www.corvane-hvac.com</div>
    </div>

    <div class="divider"></div>

    <div class="address">
      <div>4827 Dunmore St</div>
      <div>#215 Oakland, CA 94619</div>
    </div>

    <div class="license-band">LIC.# 584261</div>
  </section>

  <section class="card card--back">
    <div class="back-wordmark">
      <div class="back-wordmark__name">corvane</div>
      <div class="back-wordmark__tagline">home solutions</div>
    </div>
  </section>
</body>
</html>
```